Banner Pop Up Opt In Form REDESIGNS - SLEEK BLACK LOOK

Please redesign banners attached.

I am looking for a very sleek look....I do not like this collage of images on these current designs. Please keep all content same but use images that pop.

I have an acccount at www.pixvane-example.com or you can use your own images.

I like black background for somereason because it looks very sleek....but these designs should pop , build trust and credibility and have easy opt in form....SLEEK AND MODERN LOOK is what im looking for....

Target Market(s)

Consumers on websites

Requirements
Must have
• Please redesign banners attached.

Nice to have

Should not have

```html
<!DOCTYPE html>
<html lang="en">
<head>
<meta charset="utf-8">
<title>Pop Ups Preview</title>
<link rel="stylesheet" href="https://fonts.googleapis.com/css2?family=Montserrat:wght@500;600;700;800;900&family=Roboto:wght@400;500;700&display=swap">
<style>
  :root {
    --page-bg: #e2e7f1;
    --card-bg: #ffffff;
    --title-blue: #1d3a8a;
    --link-blue: #2f8fe0;
    --panel-black: #121212;
    --panel-stripe: #1c1c1c;
    --neon-green: #2fe01a;
    --offer-yellow: #ffd400;
    --submit-blue: #2f7ff5;
    --label-gray: #8b9099;
    --code-text: #444a52;
    --field-border: #e1e5ec;
    --pdf-red: #e3262b;
    --visual-top: #5f86a3;
    --visual-bottom: #24361f;
  }
  * { box-sizing: border-box; margin: 0; padding: 0; }
  html, body { width: 1200px; height: 772px; overflow: hidden; }
  body { background: var(--page-bg); position: relative; font-family: 'Roboto', Arial, sans-serif; }

  .preview-card {
    position: absolute; top: 17px; width: 554px; height: 739px;
    background: var(--card-bg);
  }
  .preview-card.first { left: 31px; }
  .preview-card.second { left: 615px; }

  .card-title {
    position: absolute; left: 24px; top: 22px;
    font-family: 'Montserrat', sans-serif; font-weight: 700; font-size: 17px;
    color: var(--title-blue); letter-spacing: 0.2px; white-space: nowrap;
  }
  .install-link {
    position: absolute; right: 58px; top: 30px;
    font-family: 'Montserrat', sans-serif; font-weight: 500; font-size: 14.3px;
    color: var(--link-blue); white-space: nowrap;
  }
  .pdf-icon { position: absolute; right: 25px; top: 21px; width: 30px; height: 38px; }

  .popup-banner {
    position: absolute; left: 24px; top: 75px; width: 506px; height: 433px;
    display: flex; overflow: hidden;
  }
  .offer-panel {
    width: 253px; height: 100%; position: relative; flex: none;
    background:
      repeating-linear-gradient(125deg, transparent 0 60px, rgba(255,255,255,0.025) 60px 120px),
      linear-gradient(135deg, var(--panel-stripe), var(--panel-black) 60%);
    color: #fff;
  }
  .headline { font-family: 'Montserrat', sans-serif; line-height: 1; position: absolute; left: 18.5px; }
  .headline .accent { color: var(--neon-green); font-weight: 900; display: block; white-space: nowrap; }
  .headline .main { color: #fff; font-weight: 800; display: block; white-space: nowrap; }

  .first .headline { top: 22px; }
  .first .headline .accent { font-size: 48.5px; letter-spacing: -0.5px; }
  .first .headline .main { font-size: 26.5px; margin-top: 4px; letter-spacing: -0.4px; }
  .second .headline { top: 22px; }
  .second .headline .accent { font-size: 62px; letter-spacing: -1px; }
  .second .headline .main { font-size: 56px; margin-top: -4px; letter-spacing: -1.2px; }

  .accent-rule { position: absolute; left: 18.5px; width: 98px; height: 2px; background: var(--neon-green); }
  .first .accent-rule { top: 131px; }
  .second .accent-rule { top: 151px; }

  .pitch {
    position: absolute; left: 18.5px; top: 168px;
    font-size: 13.6px; line-height: 15.5px; text-transform: uppercase; white-space: nowrap;
  }
  .prize {
    position: absolute; left: 18.5px; top: 207px;
    font-weight: 700; font-size: 14.6px; line-height: 16px; color: var(--offer-yellow);
    text-transform: uppercase; white-space: nowrap;
  }
  .optin-form { position: absolute; left: 18.5px; top: 251px; width: 220px; }
  .field {
    height: 25px; background: #fff; color: #444; font-size: 9.5px;
    padding-left: 9px; line-height: 25px; margin-bottom: 6px;
  }
  .submit-button {
    height: 25px; background: var(--submit-blue); color: #fff; margin-top: 1px;
    font-weight: 700; font-size: 9px; text-align: center; line-height: 25px; letter-spacing: 0.3px;
  }
  .disclaimer {
    position: absolute; left: 18.5px; top: 384px; width: 232px;
    font-size: 9.9px; line-height: 12px;
  }

  .offer-visual {
    flex: 1;
    background: linear-gradient(180deg, var(--visual-top), var(--visual-bottom));
  }

  .install-note {
    position: absolute; left: 24px; top: 524px; width: 520px;
    font-family: 'Montserrat', sans-serif; font-weight: 700; font-size: 13.3px; line-height: 23.5px;
    color: var(--label-gray); text-transform: uppercase;
  }
  .embed-code {
    position: absolute; left: 25px; top: 576px; width: 504px; height: 112px;
    border: 1px solid var(--field-border); border-radius: 3px;
    padding: 6px 11px; font-family: 'Montserrat', sans-serif; font-weight: 500;
    font-size: 14.2px; line-height: 20.5px; color: var(--code-text); white-space: pre; overflow: hidden;
  }
  .copy-button {
    position: absolute; right: 25px; top: 693px;
    font-family: 'Montserrat', sans-serif; font-weight: 700; font-size: 12.5px;
    color: var(--link-blue); letter-spacing: 0.8px;
  }
</style>
</head>
<body>

<section class="preview-card first">
  <h2 class="card-title">POP UPS PREVIEW</h2>
  <span class="install-link">Step By Step Installation</span>
  <svg class="pdf-icon" viewBox="0 0 30 38" aria-hidden="true">
    <path d="M2 4h18l7 7v24H2z" fill="#fff" stroke="#6b6f75" stroke-width="1.6"/>
    <path d="M8 22c3-8 5-10 6-4s5 6 8 5" fill="none" stroke="var(--pdf-red)" stroke-width="1.6"/>
    <text x="14.5" y="33" font-family="Roboto, sans-serif" font-size="7" font-weight="700" text-anchor="middle" fill="#444">PDF</text>
    <path d="M25 1v7M22 5l3 3 3-3" fill="none" stroke="var(--pdf-red)" stroke-width="1.6"/>
  </svg>

  <div class="popup-banner">
    <div class="offer-panel">
      <h1 class="headline"><span class="accent">WANT A</span><span class="main">GREAT OFFER?</span></h1>
      <div class="accent-rule"></div>
      <p class="pitch">Subscribe to our newsletter<br>and&nbsp; receive&nbsp; a&nbsp; complimentary</p>
      <p class="prize">7&nbsp; Night Resort / Condo Stay<br>3500 + Locations</p>
      <div class="optin-form">
        <div class="field">Name</div>
        <div class="field">Email</div>
        <div class="field">Phone</div>
        <div class="submit-button">SUBMIT</div>
      </div>
      <p class="disclaimer">We will send an email and a text message win the offer &amp; instructions on how to redeem.</p>
    </div>
    <div class="offer-visual" role="img" aria-label="Resort getaway photo: pool, palms and a bright guest suite"></div>
  </div>

  <p class="install-note">Install this script in between the body tags on every single page that you want the pop up to work on</p>
  <div class="embed-code">&lt;script src="https://www.sunharborrewardsdemo.biz/dashboard
/popup/popup_shr1e669a6bba.js" id="shr_popup_helper" data-
id="4db443bc045a3a64ad52d621049649b0_1" &gt;&lt;/script&gt;</div>
  <span class="copy-button">COPY CODE</span>
</section>

<section class="preview-card second">
  <h2 class="card-title">POP UPS PREVIEW</h2>
  <span class="install-link">Step By Step Installation</span>
  <svg class="pdf-icon" viewBox="0 0 30 38" aria-hidden="true">
    <path d="M2 4h18l7 7v24H2z" fill="#fff" stroke="#6b6f75" stroke-width="1.6"/>
    <path d="M8 22c3-8 5-10 6-4s5 6 8 5" fill="none" stroke="var(--pdf-red)" stroke-width="1.6"/>
    <text x="14.5" y="33" font-family="Roboto, sans-serif" font-size="7" font-weight="700" text-anchor="middle" fill="#444">PDF</text>
    <path d="M25 1v7M22 5l3 3 3-3" fill="none" stroke="var(--pdf-red)" stroke-width="1.6"/>
  </svg>

  <div class="popup-banner">
    <div class="offer-panel">
      <h1 class="headline"><span class="accent">ENTER</span><span class="main">TO WIN</span></h1>
      <div class="accent-rule"></div>
      <p class="pitch">Subscribe to our newsletter<br>to enter to win a</p>
      <p class="prize">7&nbsp; Night Resort / Condo Stay<br>3500 + Locations</p>
      <div class="optin-form">
        <div class="field">Name</div>
        <div class="field">Email</div>
        <div class="field">Phone</div>
        <div class="submit-button">SUBMIT</div>
      </div>
      <p class="disclaimer">We will send an email and a text message win the offer &amp; instructions on how to redeem.</p>
    </div>
    <div class="offer-visual" role="img" aria-label="Resort getaway photo: pool, palms and a bright guest suite"></div>
  </div>

  <p class="install-note">Install this script in between the body tags on every single page that you want the pop up to work on</p>
  <div class="embed-code">&lt;script src="https://www.sunharborrewardsdemo.biz/dashboard
/popup/popup_shr1e669a6bba.js" id="shr_popup_helper" data-
id="4db443bc045a3a64ad52d621049649b0_2" &gt;&lt;/script&gt;</div>
  <span class="copy-button">COPY CODE</span>
</section>

</body>
</html>
```